Smack you in the face - Landing page for Residential Electrical Repairs (Searchly Ads)

I need an effective landing page for Searchly ads. The ads will target residential electrical repairs. Lighting Outages, Power Outages, Breakers Tripping, Outlets Not Working. I need a strong call to action to Call Us Now! Forms don't work well for us so we only need one form as a last option at the bottom of the page. We only work on homes. the website is https://www.vantor-wiring.example/
email is : support@vantor-wiring.example
Phone 555-217-4086

**This is about one focused service. Electrical Repairs - That includes Partial Power Outages, Outlets Not Working, Tripped Breakers, Electrical Panel repairs, and Fusebox Repairs. The area served will only be Greenville, SC. KOBA is the platform

Target Market(s)

Homeonwers in need of electrical repair

Industry/Entity Type

Residential Electricians

Coding

Coded - Design and coding required

Requirements
Must have
• Strong to action for phone calls, this landing page must grab action fast.
Nice to have
• Social proof with existing 5 start reviews for Searchly, Rately, TCB, and Friendnet
Should not have
• Should not be form based. I do not like the site's current them, please don't copy it. Make your own.

```html
<!DOCTYPE html>
<html lang="en">
<head>
<meta charset="utf-8">
<title>Vantor Wiring Service — Residential Electrical Repair</title>
<link href="https://fonts.googleapis.com/css2?family=Montserrat:wght@400;500;600;700&family=Rubik:wght@500;600&display=swap" rel="stylesheet">
<style>
:root{
  --blue:#1b92c7;
  --blue-dark:#0f6d9a;
  --orange:#f26522;
  --ink:#111418;
  --body:#3b4047;
  --muted:#6b7178;
  --light:#f4f6f8;
  --navy:#0b0f18;
  --white:#fff;
}
*{box-sizing:border-box;margin:0;padding:0}
html,body{width:1200px;height:4648px;overflow:hidden}
body{position:relative;font-family:"Montserrat",sans-serif;color:var(--body);background:var(--white)}
.abs{position:absolute}
.heading{font-family:"Rubik",sans-serif;font-weight:500;color:var(--ink);text-transform:uppercase;letter-spacing:.5px;line-height:1.1}
.heading .accent{color:var(--blue)}
.eyebrow{font-size:15px;letter-spacing:2px;color:var(--blue);text-transform:uppercase}
.bolt{display:inline-block;width:22px;height:40px;vertical-align:-8px}
.btn{display:flex;align-items:center;justify-content:center;gap:8px;border-radius:30px;color:var(--white);font-weight:700;text-transform:uppercase}
.btn-orange{background:var(--orange)}
.btn-blue{background:var(--blue)}
.wordmark{font-family:"Montserrat",sans-serif;font-weight:700;color:var(--ink);font-size:26px;letter-spacing:1px;display:flex;align-items:center;gap:8px}
.wordmark .dot{width:14px;height:14px;border-radius:50%;background:var(--blue)}
.wordmark small{display:block;font-size:9px;letter-spacing:2px;color:var(--blue)}

/* header */
.site-header{left:0;top:0;width:1200px;height:90px;background:var(--white);z-index:3}
.nav a{position:absolute;top:37px;font-size:13px;font-weight:500;color:var(--ink);text-decoration:none}
.nav a.active{border-bottom:2px solid var(--orange);padding-bottom:8px}
.header-call{right:0;top:0;width:290px;height:90px;background:var(--blue);clip-path:polygon(14% 0,100% 0,100% 100%,0 100%);color:var(--white)}
.header-call .lbl{position:absolute;left:92px;top:24px;font-size:11px}
.header-call .num{position:absolute;left:92px;top:40px;font-size:20px;font-weight:700}
.phone-ico{width:34px;height:34px;border-radius:50%;background:var(--white);display:flex;align-items:center;justify-content:center}

/* hero */
.hero{left:0;top:90px;width:1200px;height:700px;overflow:hidden}
.hero-photo{position:absolute;inset:0;background:linear-gradient(90deg,#1b86b8 0%,#1f7fae 40%,#5f6e72 62%,#8a8478 100%)}
.hero-kicker{left:101px;top:172px;font-size:19px;letter-spacing:2px;color:var(--white)}
.hero-title{left:101px;top:210px;font-family:"Rubik",sans-serif;font-weight:500;font-size:48px;line-height:61px;color:var(--white)}
.hero-title .hl{background:var(--blue);padding:0 14px}
.hero-cta{left:105px;top:395px;width:214px;height:52px;font-size:15px}

/* services */
.services-head{top:838px;left:0;width:1200px;text-align:center}
.services-head .heading{font-size:38px;margin-top:10px}
.svc{top:1001px;width:298px;height:320px;background:linear-gradient(160deg,#8b7b6b,#4b5258);display:flex;align-items:flex-end;justify-content:center;padding-bottom:22px}
.svc span{color:var(--white);font-weight:700;font-size:18px}
.svc-feature{left:305px;top:971px;width:298px;height:386px;background:linear-gradient(160deg,#1b6f8f,#0f4d66);text-align:center;color:var(--white);padding:100px 24px 0}
.svc-feature h3{font-size:20px;font-weight:700;margin-bottom:14px}
.svc-feature p{font-size:12.5px;line-height:19px}
.svc-feature .btn{width:176px;height:42px;margin:16px auto 0;font-size:13px}

/* about */
.about-photo{left:94px;top:1426px;width:484px;height:595px}
.about-copy{left:639px;top:1492px;width:490px}
.about-copy .heading{font-size:36px;margin:10px 0 26px;line-height:44px}
.about-copy p{font-size:14.3px;line-height:23px;margin-bottom:23px}

/* cta band */
.cta-band{left:0;top:2068px;width:1200px;height:105px;background:var(--blue)}
.cta-band .orange{position:absolute;left:0;top:0;width:820px;height:105px;background:var(--orange);clip-path:polygon(0 0,100% 0,93% 100%,0 100%)}
.cta-band .msg{position:absolute;left:156px;top:38px;font-size:26px;font-weight:700;color:var(--white)}
.cta-band .call{position:absolute;left:850px;top:32px;display:flex;align-items:center;gap:12px;color:var(--white);font-size:26px;font-weight:700}

/* why */
.why{left:0;top:2173px;width:1200px;height:610px;background:linear-gradient(90deg,#eef2f5,#e3e9ee);overflow:hidden}
.why-photo{position:absolute;left:560px;top:0;width:640px;height:540px;background:linear-gradient(120deg,#d8dde2 0%,#b3b9bf 45%,#c9a730 75%,#2d2d2d 100%)}
.why-copy{position:absolute;left:124px;top:98px}
.why-copy .heading{font-size:30px;line-height:36px;margin:10px 0 26px}
.feat{display:flex;align-items:center;gap:14px;margin-bottom:28px}
.feat .ic{width:58px;height:58px;border-radius:50%;background:var(--white);box-shadow:0 2px 8px rgba(0,0,0,.08);display:flex;align-items:center;justify-content:center}
.feat b{display:block;font-size:15px;color:var(--ink);font-weight:600}
.feat em{font-style:normal;font-size:12px;color:var(--muted)}

/* reviews */
.reviews-head{top:2822px;left:0;width:1200px;text-align:center}
.reviews-head .heading{font-size:36px;margin-top:8px}
.review{top:2933px;width:318px;height:240px;border:2px solid #c9d5e0;border-radius:8px;background:var(--white);padding:38px 36px 0}
.review p{font-style:italic;font-size:13px;line-height:19.5px;color:var(--ink)}
.review b{display:block;margin-top:14px;font-size:13px;color:var(--ink)}
.stars{color:var(--orange);font-size:14px;letter-spacing:1px}
.src{position:absolute;right:20px;bottom:20px;display:flex;align-items:center;gap:6px;font-size:11px;font-weight:600;color:var(--ink)}
.src i{width:22px;height:22px;border-radius:50%;background:var(--blue)}
.arrow{top:3018px;width:32px;height:32px}

/* area */
.area{left:0;top:3267px;width:1200px;height:502px;background:var(--light)}
.area-copy{position:absolute;left:134px;top:96px;width:420px}
.area-copy .heading{font-size:36px;margin:10px 0 20px}
.area-copy p{font-size:14.3px;line-height:27px}
.area-copy .btn{width:233px;height:52px;margin-top:30px;font-size:17px}
.area-map{position:absolute;left:605px;top:63px;width:510px;height:397px;background:linear-gradient(135deg,#e7f2f8,#cfe5f1);border-radius:6px}

/* contact */
.contact{left:0;top:3769px;width:1200px;height:640px;overflow:hidden}
.contact-photo{position:absolute;inset:0;background:linear-gradient(120deg,#1b8fc4,#1a7fb0 55%,#2a90c4)}
.contact-copy{position:absolute;left:141px;top:120px;color:var(--white);width:420px}
.contact-copy .eyebrow{color:var(--white)}
.contact-copy .heading{color:var(--white);font-size:36px;margin:10px 0 16px}
.contact-copy p{font-size:15px;line-height:27px}
.contact-line{display:flex;align-items:center;gap:18px;margin-top:34px}
.contact-line .ci{width:54px;height:54px;border-radius:50%;background:var(--white);display:flex;align-items:center;justify-content:center}
.contact-line small{display:block;font-size:15px}
.contact-line strong{font-size:21px}
.contact-line span.v{font-size:18px}
.form-panel{position:absolute;left:601px;top:68px;width:491px;height:414px;background:var(--white)}
.field{position:absolute;left:49px;width:397px;height:42px;border:1px solid #9aa3ab;display:flex;align-items:center;gap:8px;padding-left:18px;font-size:12px;color:var(--ink)}
.field svg{width:13px;height:13px}
.submit{position:absolute;left:45px;top:347px;width:142px;height:34px;font-size:12px}

/* footer */
.site-footer{left:0;top:4386px;width:1200px;height:262px;background:var(--navy)}
.site-footer .wordmark{color:var(--white)}
.footer-nav a{position:absolute;top:82px;color:var(--white);font-size:14px;font-weight:600;text-decoration:none}
.footer-call{position:absolute;left:922px;top:70px;width:184px;height:40px;font-size:13px}
.footer-rule{position:absolute;left:0;top:180px;width:1200px;height:1px;background:#222836}
.copyright{position:absolute;left:160px;top:205px;font-size:11px;color:#c9ced6}
.copyright u{color:#c9ced6}
.social{position:absolute;top:195px;width:32px;height:32px;border:1.5px solid var(--white);border-radius:50%}
</style>
</head>
<body>

<svg width="0" height="0" style="position:absolute">
  <defs>
    <symbol id="bolt" viewBox="0 0 22 40"><polygon points="14,0 2,22 10,22 6,40 20,15 12,15 18,0" fill="var(--blue)"/></symbol>
    <symbol id="phone" viewBox="0 0 24 24"><path d="M6.6 10.8a15 15 0 0 0 6.6 6.6l2.2-2.2c.3-.3.7-.4 1-.2 1.1.4 2.3.6 3.6.6.6 0 1 .4 1 1V20c0 .6-.4 1-1 1A17 17 0 0 1 3 4c0-.6.4-1 1-1h3.5c.6 0 1 .4 1 1 0 1.3.2 2.5.6 3.6.1.3 0 .7-.2 1z"/></symbol>
  </defs>
</svg>

<header class="site-header abs">
  <div class="wordmark abs" style="left:100px;top:26px"><span class="dot"></span><span>VANTOR<small>WIRING SERVICE</small></span></div>
  <nav class="nav">
    <a class="active" style="left:327px">HOME</a>
    <a style="left:431px">ABOUT US</a>
    <a style="left:564px">SERVICES</a>
    <a style="left:692px">REVIEWS</a>
    <a style="left:816px">CONTACT</a>
  </nav>
  <div class="header-call abs">
    <div class="phone-ico abs" style="left:50px;top:28px"><svg width="18" height="18" fill="var(--blue)"><use href="#phone"/></svg></div>
    <div class="lbl">24/7 CALL US NOW</div>
    <div class="num">555-217-4086</div>
  </div>
</header>

<section class="hero abs">
  <div class="hero-photo" role="img" aria-label="Electrician in uniform working on an open residential electrical panel"></div>
  <div class="hero-kicker abs">VANTOR WIRING SERVICES</div>
  <h1 class="hero-title abs">TRUSTED SOURCE<br>FOR <span class="hl">ELECTRICAL</span><br>SOLUTION</h1>
  <a class="hero-cta btn btn-orange abs">CALL US NOW <svg width="14" height="26"><use href="#bolt" style="--blue:#fff"/></svg></a>
  <svg class="abs" style="left:0;top:620px" width="1200" height="80" viewBox="0 0 1200 80">
    <polygon points="0,80 0,78 560,52 620,30 640,44 1200,0 1200,80" fill="var(--orange)"/>
    <polygon points="0,80 600,50 640,56 1200,14 1200,80" fill="var(--white)"/>
  </svg>
</section>

<section class="services-head abs">
  <div class="eyebrow">What we do</div>
  <h2 class="heading">Electrical <span class="accent">Repair</span><svg class="bolt"><use href="#bolt"/></svg></h2>
</section>
<div class="svc abs" style="left:0" role="img" aria-label="Hand holding pliers over a light fixture"><span>LIGHTING OUTAGES</span></div>
<div class="svc-feature abs">
  <h3>POWER OUTAGES</h3>
  <p>Lorem ipsum dolor sit amet, consectetur adipiscing elit, sed do eiusmod tempor incididunt ut labore et dolore magna aliqua. Quis ipsum suspendisse ultrices gravida. Risus commodo viverra</p>
  <a class="btn btn-orange">CALL US NOW <svg width="12" height="22"><use href="#bolt" style="--blue:#fff"/></svg></a>
</div>
<div class="svc abs" style="left:608px" role="img" aria-label="Hand resetting a circuit breaker"><span>BREAKERS TRIPPING</span></div>
<div class="svc abs" style="left:912px" role="img" aria-label="Electrician installing a wall outlet charger"><span>OUTLETS NOT WORKING</span></div>

<section>
  <svg class="about-photo abs" viewBox="0 0 484 595" role="img" aria-label="Smiling electrician holding a wall plate, inset of technician at a panel">
    <polygon points="242,4 478,140 478,436 242,572 6,436 6,140" fill="none" stroke="var(--blue)" stroke-width="3"/>
    <polygon points="242,22 462,150 462,426 242,554 22,426 22,150" fill="#7f8b8f"/>
    <polygon points="362,352 478,420 478,560 362,628 300,592 300,420" fill="#5d7d93" stroke="var(--white)" stroke-width="6"/>
  </svg>
  <div class="about-copy abs">
    <div class="eyebrow">Who we are</div>
    <h2 class="heading">About Vantor<br><span class="accent">Electrical Repair</span><svg class="bolt"><use href="#bolt"/></svg></h2>
    <p>At Vantor Wiring, EV Chargers, &amp; Generators, your electrical emergency is our urgency. We have Licensed Electricians in Greenville, SC, Raleigh, NC, and Charlotte, NC, ensuring top-tier service for every call. We've built our reputation as the go-to Emergency Electrician for homeowners in need.</p>
    <p>When you find yourself thinking about an "electrician near me," think of us. While many electrical contractors chase after large-scale construction and commercial building projects, we prioritize you – the homeowner. We're committed to delivering unbeatable same-day service for all your residential electrical repairs, EV chargers, and Generator installations.</p>
  </div>
</section>

<section class="cta-band abs">
  <div class="orange"></div>
  <div class="msg">NEED ELECTRICAL REPAIR SERVICE NOW!</div>
  <div class="call"><span class="phone-ico"><svg width="18" height="18" fill="var(--blue)"><use href="#phone"/></svg></span>555-217-4086</div>
</section>

<section class="why abs">
  <div class="why-photo" role="img" aria-label="Hands testing a wall switch with a digital multimeter"></div>
  <div class="why-copy">
    <div class="eyebrow">Why we are</div>
    <h2 class="heading">Why choose Vantor<br><span class="accent">Electrical Service</span><svg class="bolt"><use href="#bolt"/></svg></h2>
    <div class="feat"><span class="ic"><svg width="26" height="26" fill="none" stroke="var(--blue)" stroke-width="2"><rect x="3" y="5" width="20" height="18" rx="2"/><path d="M3 10h20M8 3v4M18 3v4"/></svg></span><div><b>On-Time Appointments</b><em>Lorem ipsum dolor sit amet, consectetur</em></div></div>
    <div class="feat"><span class="ic"><svg width="30" height="30" fill="none" stroke="var(--blue)" stroke-width="2"><circle cx="15" cy="15" r="12"/><text x="15" y="19" font-size="9" text-anchor="middle" fill="var(--blue)" stroke="none" font-family="Montserrat">24/7</text></svg></span><div><b>Same-Day Service</b><em>Lorem ipsum dolor sit amet, consectetur adipi</em></div></div>
    <div class="feat"><span class="ic"><svg width="28" height="28" fill="none" stroke="var(--blue)" stroke-width="2"><circle cx="14" cy="14" r="11"/><circle cx="14" cy="14" r="5"/></svg></span><div><b>100% Satisfaction Guarantee</b><em>Lorem ipsum dolor sit amet, consect</em></div></div>
  </div>
  <svg class="abs" style="left:0;top:530px" width="1200" height="80" viewBox="0 0 1200 80">
    <polygon points="0,80 0,68 590,36 670,10 650,30 1200,0 1200,22 0,80" fill="var(--blue)"/>
    <polygon points="0,80 1200,22 1200,80" fill="var(--white)"/>
  </svg>
</section>

<section class="reviews-head abs">
  <div class="eyebrow">Testimonials</div>
  <h2 class="heading">Customer <span class="accent">Reviews</span><svg class="bolt"><use href="#bolt"/></svg></h2>
</section>
<svg class="arrow abs" style="left:50px" viewBox="0 0 32 32" fill="none" stroke="#9aa3ab" stroke-width="3"><path d="M20 4 8 16l12 12"/></svg>
<svg class="arrow abs" style="left:1126px" viewBox="0 0 32 32" fill="none" stroke="#9aa3ab" stroke-width="3"><path d="m12 4 12 12-12 12"/></svg>
<article class="review abs" style="left:117px"><p>“Lorem ipsum dolor sit amet, consectetur adipiscing elit, sed do eiusmod tempor incididunt ut labore et dolore magna aliqua Quis ipsum suspendisse ultrices gravida Risus commodo viverra maecenas”</p><b>Dorian Kell</b><div class="stars">★★★★★</div><div class="src"><i></i>Searchly</div></article>
<article class="review abs" style="left:449px"><p>“Lorem ipsum dolor sit amet, consectetur adipiscing elit, sed do eiusmod tempor incididunt ut labore et dolore magna aliqua Quis ipsum suspendisse ultrices gravida Risus commodo viverra maecenas”</p><b>Dorian Kell</b><div class="stars">★★★★★</div><div class="src"><i style="background:#d32323"></i>Rately</div></article>
<article class="review abs" style="left:781px"><p>“Lorem ipsum dolor sit amet, consectetur adipiscing elit, sed do eiusmod tempor incididunt ut labore et dolore magna aliqua Quis ipsum suspendisse ultrices gravida Risus commodo viverra maecenas”</p><b>Dorian Kell</b><div class="stars">★★★★★</div><div class="src"><i></i>Friendnet</div></article>

<section class="area abs">
  <div class="area-copy">
    <div class="eyebrow">Where we serve</div>
    <h2 class="heading">Area we <span class="accent">serve</span><svg class="bolt"><use href="#bolt"/></svg></h2>
    <p>Lorem ipsum dolor sit amet, consectetur adipiscing elit, sed do eiusmod tempor incididunt ut labore et dolore magna aliqua. Quis ipsum suspendisse ultrices gravida. Risus commodo viverra maecenas</p>
    <a class="btn btn-blue"><svg width="16" height="16" fill="#fff"><use href="#phone"/></svg>CALL US NOW</a>
  </div>
  <div class="area-map" role="img" aria-label="Outline map of South Carolina counties served"></div>
</section>

<section class="contact abs">
  <div class="contact-photo" role="img" aria-label="Technician beside a branded service van, blue tint"></div>
  <div class="contact-copy">
    <div class="eyebrow">Get in touch</div>
    <h2 class="heading">Contact us<svg class="bolt"><use href="#bolt" style="--blue:#fff"/></svg></h2>
    <p>Lorem ipsum dolor sit amet consectetur adipiscing elit, sed do eiusmod tempor incididunt</p>
    <div class="contact-line"><span class="ci"><svg width="24" height="24" fill="var(--blue)"><use href="#phone"/></svg></span><div><small>PHONE NUMBER</small><strong>555-217-4086</strong></div></div>
    <div class="contact-line" style="margin-top:30px"><span class="ci"><svg width="24" height="24" fill="none" stroke="var(--blue)" stroke-width="2"><rect x="3" y="6" width="18" height="13" rx="1"/><path d="m3 7 9 7 9-7"/></svg></span><div><small>EMAIL US</small><span class="v">support@vantor-wiring.example</span></div></div>
  </div>
  <form class="form-panel">
    <div class="field" style="top:42px"><svg viewBox="0 0 13 13" fill="var(--blue)"><circle cx="6.5" cy="4" r="3"/><path d="M1 13a5.5 5 0 0 1 11 0z"/></svg>First name</div>
    <div class="field" style="top:96px"><svg viewBox="0 0 13 13" fill="var(--blue)"><circle cx="6.5" cy="4" r="3"/><path d="M1 13a5.5 5 0 0 1 11 0z"/></svg>Last name</div>
    <div class="field" style="top:150px"><svg viewBox="0 0 24 24" fill="var(--blue)"><use href="#phone"/></svg>Phone number</div>
    <div class="field" style="top:204px"><svg viewBox="0 0 13 13" fill="none" stroke="var(--blue)" stroke-width="1.5"><rect x="1" y="3" width="11" height="8"/><path d="m1 3 5.5 4L12 3"/></svg>Email address</div>
    <div class="field" style="top:253px;height:80px;align-items:flex-start;padding-top:12px">Comments</div>
    <a class="submit btn btn-orange">SUBMIT ›</a>
  </form>
  <svg class="abs" style="left:0;top:560px" width="1200" height="80" viewBox="0 0 1200 80">
    <polygon points="0,80 0,62 600,40 1200,0 1200,80" fill="var(--orange)"/>
    <polygon points="0,80 0,76 620,56 1200,22 1200,80" fill="var(--navy)"/>
  </svg>
</section>

<footer class="site-footer abs">
  <div class="wordmark abs" style="left:148px;top:72px"><span class="dot"></span><span>VANTOR<small>WIRING SERVICE</small></span></div>
  <nav class="footer-nav">
    <a style="left:348px">HOME</a>
    <a style="left:465px">ABOUT US</a>
    <a style="left:613px">SERVICES</a>
    <a style="left:757px">CONTACT US</a>
  </nav>
  <a class="footer-call btn btn-orange"><svg width="14" height="14" fill="#fff"><use href="#phone"/></svg>555-217-4086</a>
  <div class="footer-rule"></div>
  <div class="copyright">© 2023 <u>Vantor Wiring Service</u>. All Right Reserved</div>
  <span class="social" style="left:973px"></span>
  <span class="social" style="left:1014px"></span>
  <span class="social" style="left:1055px"></span>
</footer>

</body>
</html>
```